We want to design total new business card and logo for Kestrel Building Services Ltd

Our company name Kestrel Building Services Ltd. Design new logo and business card , need hi-end luxury style art for architecture and construction industry. The card should simple but stylish. Our business focus on CONNECT tradesman to construction company, help marketing construction company tender oversea projects, managing franchise in construction sector, delivery amazing services to our client, so Logo should show the CONNECTION IDEA, CONNECTING PEOPLE, LUXURY. Visit our website for more information: kestrelgroup.example.nz

Target Market(s)

Directors or managers

Industry/Entity Type

Construction Company

Contact Information for Business Card

Name, Title, Mobile, Email, Website

Font styles to use
Serif

Colors

Designer to choose colors to be used in the design.

Requirements
Must have
• Simple and luxury, connection icon
Nice to have
• Special materials, plastic card, look through,...
• Look new ideas.

```html
<!DOCTYPE html>
<html lang="en">
<head>
<meta charset="utf-8">
<title>Kestrel Building Services Ltd — Business Card</title>
<link href="https://fonts.googleapis.com/css2?family=Work+Sans:wght@400;500;600&display=swap" rel="stylesheet">
<style>
  :root {
    --backdrop: #1c1c1c;
    --card: #262626;
    --card-edge: #303030;
    --silver: #d6d6d6;
    --text: #f2f2f2;
    --accent: #1a63c4;
  }
  * { margin: 0; padding: 0; box-sizing: border-box; }
  html, body {
    width: 1200px; height: 900px; overflow: hidden;
    background: var(--backdrop);
    font-family: "Work Sans", Arial, sans-serif;
  }
  .canvas { position: relative; width: 1200px; height: 900px; }
  .card {
    position: absolute; left: 285px;
    width: 630px; height: 360px;
    background: var(--card);
    border: 1px solid var(--card-edge);
    box-shadow: 0 18px 40px rgba(0,0,0,.55);
    overflow: hidden;
  }
  .card--front { top: 70px; }
  .card--back { top: 470px; }

  /* Front */
  .brand {
    position: absolute; left: 0; right: 0; top: 96px;
    display: flex; flex-direction: column; align-items: center;
    color: var(--silver);
  }
  .brand__dot {
    width: 58px; height: 58px; border-radius: 50%;
    background: var(--silver); margin-bottom: 26px;
  }
  .brand__name {
    font-weight: 500; font-size: 30px; letter-spacing: 2px; line-height: 1;
    text-transform: uppercase;
  }
  .brand__sub {
    font-weight: 500; font-size: 18px; letter-spacing: 9px; margin-top: 8px;
    text-transform: uppercase;
  }

  /* Back */
  .contact { position: absolute; left: 44px; top: 104px; color: var(--text); }
  .contact__name {
    color: var(--accent); font-weight: 500; font-size: 24px;
    text-transform: uppercase; letter-spacing: .5px;
  }
  .contact__title { font-size: 15px; margin-top: 2px; }
  .contact__address { font-size: 15px; line-height: 1.4; margin-top: 18px; }
  .contact__list { list-style: none; margin-top: 14px; font-size: 15px; line-height: 1.55; }
  .contact__list li { display: flex; align-items: center; gap: 9px; }
  .contact__icon { width: 12px; height: 12px; flex: none; }

  .back-mark {
    position: absolute; right: 28px; top: 40px;
    width: 280px; height: 280px; border-radius: 50%;
    background: var(--silver);
    display: flex; align-items: center; justify-content: center;
  }
  .back-mark__name {
    font-weight: 500; font-size: 19px; letter-spacing: 1px; text-transform: uppercase;
    color: var(--card); text-align: center; line-height: 1.3;
  }
</style>
</head>
<body>
<main class="canvas">
  <section class="card card--front" aria-label="Card front">
    <div class="brand">
      <span class="brand__dot" aria-hidden="true"></span>
      <span class="brand__name">Kestrel Building</span>
      <span class="brand__sub">Services Ltd</span>
    </div>
  </section>

  <section class="card card--back" aria-label="Card back">
    <div class="contact">
      <h1 class="contact__name">Daniel Hartley</h1>
      <p class="contact__title">Director</p>
      <p class="contact__address">218 Harbour View Rd<br>Wilmington, NC 28401</p>
      <ul class="contact__list">
        <li>
          <svg class="contact__icon" viewBox="0 0 12 12" aria-hidden="true"><path d="M3 1 L5 3.5 L4 5 Q5 7 7 8 L8.5 7 L11 9 L9.5 11 Q4 10.5 1 3 Z" fill="var(--accent)"/></svg>
          +64 21 418 5120
        </li>
        <li>
          <svg class="contact__icon" viewBox="0 0 12 12" aria-hidden="true"><rect x="3" y="1" width="6" height="3" fill="var(--accent)"/><rect x="1" y="4.5" width="10" height="4.5" rx="1" fill="var(--accent)"/><rect x="3" y="8" width="6" height="3" fill="var(--accent)"/></svg>
          +64 9 377 2046
        </li>
        <li>
          <svg class="contact__icon" viewBox="0 0 12 12" aria-hidden="true"><rect x="1" y="2.5" width="10" height="7" fill="none" stroke="var(--accent)" stroke-width="1.2"/><path d="M1 2.5 L6 6.5 L11 2.5" fill="none" stroke="var(--accent)" stroke-width="1.2"/></svg>
          info@kestrelgroup.example.nz
        </li>
        <li>
          <svg class="contact__icon" viewBox="0 0 12 12" aria-hidden="true"><circle cx="6" cy="6" r="5" fill="none" stroke="var(--accent)" stroke-width="1.1"/><ellipse cx="6" cy="6" rx="2.2" ry="5" fill="none" stroke="var(--accent)" stroke-width="1"/><path d="M1 6 H11" stroke="var(--accent)" stroke-width="1"/></svg>
          www.kestrelgroup.example.nz
        </li>
      </ul>
    </div>
    <div class="back-mark">
      <span class="back-mark__name">Kestrel<br>Building<br>Services Ltd</span>
    </div>
  </section>
</main>
</body>
</html>
```